KLV Plant Services

We are a heavy diesel mechanical business with additional air con certificates, remapping engine rebuilt

Contact Information for Business Card

Company Name, Director Name, Managing Director, Contact details, email and website

Font styles to use
Serif
Script

```html
<!DOCTYPE html>
<html lang="en">
<head>
<meta charset="utf-8">
<title>KLV Plant Services – Business Card</title>
<link rel="stylesheet" href="https://fonts.googleapis.com/css2?family=Playfair+Display:wght@700&family=Lora:wght@400;500&family=Great+Vibes&display=swap">
<style>
  :root {
    --navy: #2b2a80;
    --navy-deep: #24206b;
    --navy-soft: #4a5bc0;
    --ink: #1a1a1f;
    --paper: #ffffff;
    --stage: #e4e5ea;
    --rule: #2a2a2a;
  }
  * { box-sizing: border-box; margin: 0; padding: 0; }
  html, body { width: 1200px; height: 780px; overflow: hidden; }
  body {
    background: var(--stage);
    font-family: "Lora", Georgia, serif;
    color: var(--ink);
    display: flex;
    align-items: center;
    justify-content: center;
    gap: 40px;
  }
  .card {
    position: relative;
    width: 540px;
    height: 310px;
    border-radius: 18px;
    overflow: hidden;
    box-shadow: 0 6px 20px rgba(20, 20, 40, 0.18);
  }
  .card--front { background: var(--paper); }
  .card--back {
    background: var(--navy-deep);
    display: flex;
    align-items: center;
    justify-content: center;
  }

  .brand {
    position: absolute;
    left: 32px;
    top: 58px;
    display: flex;
    align-items: center;
    gap: 12px;
  }
  .brand__mark {
    width: 26px;
    height: 26px;
    border-radius: 50%;
    border: 3px solid var(--navy);
    flex: none;
  }
  .brand__name {
    font-family: "Playfair Display", Georgia, serif;
    font-weight: 700;
    font-size: 26px;
    line-height: 1.1;
    color: var(--navy);
    width: 150px;
  }

  .divider {
    position: absolute;
    left: 0; top: 0;
    width: 540px; height: 310px;
    pointer-events: none;
  }

  .address-band {
    position: absolute;
    left: 0;
    bottom: 30px;
    width: 350px;
    height: 24px;
    background: var(--navy);
    color: var(--paper);
    font-family: "Lora", Georgia, serif;
    font-size: 11.5px;
    line-height: 24px;
    padding-left: 22px;
    letter-spacing: 0.2px;
  }

  .contact {
    position: absolute;
    left: 276px;
    top: 74px;
  }
  .contact__name {
    font-family: "Playfair Display", Georgia, serif;
    font-weight: 700;
    font-size: 31px;
    color: var(--navy);
    line-height: 1.05;
  }
  .contact__role {
    font-family: "Great Vibes", cursive;
    font-size: 21px;
    color: var(--ink);
    line-height: 1.1;
    margin-top: 2px;
  }
  .contact__list {
    list-style: none;
    margin-top: 12px;
  }
  .contact__item {
    display: flex;
    align-items: center;
    gap: 8px;
    font-size: 14px;
    line-height: 23px;
  }
  .contact__icon { width: 13px; height: 13px; flex: none; }

  .back-brand {
    display: flex;
    align-items: center;
    gap: 16px;
  }
  .back-brand__mark {
    width: 40px;
    height: 40px;
    border-radius: 50%;
    border: 4px solid var(--navy-soft);
  }
  .back-brand__name {
    font-family: "Playfair Display", Georgia, serif;
    font-weight: 700;
    font-size: 40px;
    color: var(--navy-soft);
    line-height: 1.1;
  }
</style>
</head>
<body>

  <section class="card card--front" aria-label="Business card front">
    <div class="brand">
      <span class="brand__mark"></span>
      <span class="brand__name">KLV Plant Services</span>
    </div>

    <svg class="divider" viewBox="0 0 540 310" aria-hidden="true">
      <line x1="258" y1="70" x2="188" y2="228" stroke="var(--rule)" stroke-width="1"/>
    </svg>

    <div class="contact">
      <div class="contact__name">Tomas Reichl</div>
      <div class="contact__role">Managing Director</div>
      <ul class="contact__list">
        <li class="contact__item">
          <svg class="contact__icon" viewBox="0 0 16 16" aria-hidden="true">
            <path fill="var(--navy)" d="M3.6 1.2l2.3 2.6-1.3 1.7c.9 2 2.3 3.4 4.2 4.3l1.7-1.3 2.6 2.3-1.2 2.4C7 13.2 2.8 9 1.2 3.6z"/>
          </svg>
          <span>0400 126 958</span>
        </li>
        <li class="contact__item">
          <svg class="contact__icon" viewBox="0 0 16 16" aria-hidden="true">
            <circle cx="8" cy="8" r="6.5" fill="none" stroke="var(--navy)" stroke-width="1.6"/>
            <ellipse cx="8" cy="8" rx="2.6" ry="6.5" fill="none" stroke="var(--navy)" stroke-width="1.2"/>
            <line x1="1.5" y1="8" x2="14.5" y2="8" stroke="var(--navy)" stroke-width="1.2"/>
          </svg>
          <span>www.klvplantservices.net</span>
        </li>
        <li class="contact__item">
          <svg class="contact__icon" viewBox="0 0 16 16" aria-hidden="true">
            <rect x="1" y="3" width="14" height="10" rx="1.2" fill="var(--navy)"/>
            <path d="M1.8 4l6.2 5 6.2-5" fill="none" stroke="var(--paper)" stroke-width="1.2"/>
          </svg>
          <span>admin@klvplantservices.net</span>
        </li>
      </ul>
    </div>

    <div class="address-band">48 Harlow Street, Kelvale, WA 6100, Australia</div>
  </section>

  <section class="card card--back" aria-label="Business card back">
    <div class="back-brand">
      <span class="back-brand__mark"></span>
      <span class="back-brand__name">KLV Plant<br>Services</span>
    </div>
  </section>

</body>
</html>
```